Plenko - Shoe Fitting App : Foot scanning app, 3D reconstruction and Fit recommandation.

We are a startup that has developed a 3D scanning App that compares the 3d reconstructed foot to the 3D Last (mould) of a shoe to find the best match and recommend a shoe size with a graphical representation of the fit on a reconstructed foot without texturing. The challenge of this app is to have a simple and intuitive onboarding of the user with clean and crisp ui and a simple tutorial for foot scanning. 3D representation of the fit is also key. What you see is what you feel is what we would like to achieve.

Target Market(s)

Sneaker Brands and athletic shoes brands

Industry/Entity Type

Footwear

Font styles to use
Other font styles liked:
• Oswald or Droid Serif

Colors
0094D4
00A9DD
6FCCEA
C7EBF8
E9F6FB

Requirements
Must have
• Simple intuitive UI to onboard the customer to scan his bare foot (please look at attached image on how to scan the foot). You must flip your phone so that the screen is facing your foot. Start at 40cm distance form the front of your foot and turn 360% slowly to capture the foot while you feel the aptic of the iPhone. That needs to be presented with a simple animation that the user can easily understand and skip if he is a returning customer and knows how to do that. the rest of the UI is to present the result of the scanned foot for the user to use to get his fit and size. The other must have is the final result screen. Where the user will a representation of the foot (snug, loose ) of different predefined areas of the foot so he can choose the fit that he likes and not necessarily the size that we suggest. Must match website design (https://www.plenko.example)
Nice to have
• An animation of the whole process (scan-compare 3d foot with 3d shoe last(or mould) and get the 3D result of the best fit + associated size. Optionaly, an option to play with your foot and transform it (avatar like with accessories and colours)
Should not have
• Too many colours. Too much text. No gender type. No race type.

```html
<!DOCTYPE html>
<html lang="en">
<head>
<meta charset="utf-8">
<title>Plenko – Foot Scanning Screens</title>
<link href="https://fonts.googleapis.com/css2?family=Montserrat:wght@400;500;600;700;800&display=swap" rel="stylesheet">
<style>
  :root {
    --backdrop: #7b797a;
    --screen: #000000;
    --ink: #ffffff;
    --muted: #d9d9d9;
    --frame: #bdbdbd;
    --teal: #4cb3b5;
    --dot-off: #4a4a4a;
    --track: #2a2a2a;
  }
  * { box-sizing: border-box; margin: 0; padding: 0; }
  html, body { width: 800px; height: 1200px; overflow: hidden; background: var(--backdrop); }
  body { font-family: 'Montserrat', sans-serif; color: var(--ink); }
  .stage {
    position: absolute; left: 0; top: 0; width: 1568px; height: 2354px;
    transform: scale(0.5102); transform-origin: 0 0;
  }
  .screen {
    position: absolute; width: 386px; background: var(--screen);
    box-shadow: 0 30px 80px rgba(0,0,0,.45);
  }
  .brand {
    position: absolute; top: 30px; left: 0; right: 0; text-align: center;
    font-weight: 800; font-size: 54px; letter-spacing: 1px; line-height: 64px;
  }
  .card {
    position: absolute; left: 20px; top: 120px; width: 346px; height: 489px;
    border: 3px solid var(--frame); border-radius: 18px; overflow: hidden;
  }
  .abs { position: absolute; left: 0; right: 0; text-align: center; }
  .card-title { font-weight: 700; font-size: 24px; line-height: 32px; letter-spacing: .3px; }
  .card-body { font-size: 17px; line-height: 27px; padding: 0 30px; }
  .card-caps { font-size: 14px; line-height: 24px; text-transform: uppercase; }
  .art { position: absolute; left: 0; right: 0; }
  .dots { position: absolute; top: 633px; left: 0; right: 0; display: flex; justify-content: center; gap: 11px; }
  .dots span { width: 8px; height: 8px; border-radius: 50%; background: var(--dot-off); }
  .dots .on { background: var(--ink); }
  .btn {
    position: absolute; height: 56px; border-radius: 28px; background: var(--teal);
    color: var(--ink); font-weight: 700; font-size: 19px; letter-spacing: .5px;
    display: flex; align-items: center; justify-content: center;
  }
  .btn.ghost { background: #151515; border: 2px solid #6a6a6a; }
  .scan-note { position: absolute; right: 14px; bottom: 24px; width: 120px; text-align: center; font-size: 10px; font-weight: 700; line-height: 15px; }
  .eye { position: absolute; left: 29px; top: 418px; }

  .loader { position: absolute; left: 20px; top: 113px; width: 349px; height: 994px; border: 2px solid var(--ink); }
  .h-lg { font-weight: 700; font-size: 24px; line-height: 31px; letter-spacing: .5px; }
  .h-sm { font-weight: 700; font-size: 17px; line-height: 22px; letter-spacing: .3px; }
  .txt { font-size: 15px; line-height: 23px; }
  .txt-sm { font-size: 14px; line-height: 23px; padding: 0 22px; color: var(--muted); }
  .pct { font-weight: 700; font-size: 16px; line-height: 20px; }
  .bar { position: absolute; left: 19px; width: 310px; height: 14px; border: 2px solid #3a3a3a; border-radius: 7px; background: var(--track); }
  .bar.full { background: var(--teal); border-color: #888; }
  .knob { position: absolute; left: 18px; top: 164px; width: 28px; height: 28px; border-radius: 50%; background: var(--teal); }
  .rule { position: absolute; left: 26px; width: 295px; height: 2px; background: var(--teal); }
  .segment {
    position: absolute; left: 26px; top: 471px; width: 295px; height: 33px;
    border: 1px solid #444; border-radius: 17px; display: flex; align-items: center;
    font-weight: 700; font-size: 13px;
  }
  .segment span { flex: 1; text-align: center; }
  .segment .active { flex: 0 0 110px; height: 31px; line-height: 31px; border-radius: 16px; background: var(--teal); }
  .chev { position: absolute; top: 477px; }
</style>
</head>
<body>
<div class="stage">

  <!-- Lighting tip -->
  <section class="screen" style="left:159px; top:208px; height:747px;">
    <div class="brand">PLENKO</div>
    <div class="card">
      <div class="abs card-title" style="top:52px;">MAKE SURE YOU'RE<br>IN A WELL LIT AREA</div>
      <div class="abs card-body" style="top:138px;">Avoid Strong light from only one direction.This casts deep shadows that reduce accuracy of the scan.</div>
      <div class="art" role="img" aria-label="Two spotlights shining down onto a dark stage floor"
           style="top:237px; height:250px; background: radial-gradient(ellipse at 50% 95%, #7d7a66 0%, #2b2a22 35%, #0b0b08 70%), #0b0b08;"></div>
    </div>
    <div class="dots"><span class="on"></span><span></span><span></span></div>
    <div class="btn" style="left:107px; top:664px; width:172px;">NEXT</div>
  </section>

  <!-- Shoes tip -->
  <section class="screen" style="left:591px; top:208px; height:747px;">
    <div class="brand">PLENKO</div>
    <div class="card">
      <div class="abs card-title" style="top:52px;">TAKE OFF YOUR SHOES<br>AND ROLL UP PANTS</div>
      <div class="abs card-body" style="top:138px;">To Scan your feet,the camera needs to see the unique details,including your ankle.</div>
      <div class="art" role="img" aria-label="Illustration of two bare feet with rolled up jeans beside removed shoes"
           style="top:247px; height:225px; background: radial-gradient(ellipse at 50% 45%, #5a4434 0%, #1e1712 45%, #000 75%);"></div>
    </div>
    <div class="dots"><span></span><span class="on"></span><span></span></div>
    <div class="btn" style="left:107px; top:664px; width:172px;">NEXT</div>
  </section>

  <!-- Scan tip -->
  <section class="screen" style="left:1023px; top:208px; height:747px;">
    <div class="brand">PLENKO</div>
    <div class="card">
      <div class="abs card-caps" style="top:41px;">Flip the screen towards<br>your toes to smart scanning</div>
      <div class="art" role="img" aria-label="Contoured foot with a 360 degree rotation badge showing the scanning path"
           style="top:97px; height:392px; background: radial-gradient(ellipse at 50% 45%, #b49872 0%, #5e4d36 35%, #000 70%);"></div>
      <div class="scan-note">360% scanning around foot at 40 cm distance with slow speed</div>
    </div>
    <div class="dots"><span></span><span></span><span class="on"></span></div>
    <div class="btn" style="left:182px; top:664px; width:172px;">RIGHT FOOT</div>
  </section>

  <!-- Reconstruction check -->
  <section class="screen" style="left:159px; top:993px; height:747px;">
    <div class="brand">PLENKO</div>
    <div class="card">
      <div class="abs h-sm" style="top:66px; line-height:27px;">Please check that the<br>reconstruction of your<br>foot seems correct</div>
      <div class="art" role="img" aria-label="Untextured grey 3D reconstruction of a foot"
           style="left:51px; right:25px; top:192px; height:195px; background: radial-gradient(ellipse at 45% 55%, #bdbdbd 0%, #6e6e6e 40%, #000 72%);"></div>
      <svg class="eye" width="48" height="48" viewBox="0 0 48 48" aria-label="Toggle view">
        <circle cx="24" cy="24" r="22" fill="none" stroke="#4cb3b5" stroke-width="2"/>
        <path d="M14 24c3-5 7-7 10-7s7 2 10 7c-3 5-7 7-10 7s-7-2-10-7z" fill="none" stroke="#fff" stroke-width="2"/>
        <circle cx="24" cy="24" r="3" fill="#fff"/>
      </svg>
    </div>
    <div class="btn ghost" style="left:24px; top:645px; width:166px;">SCAN AGAIN</div>
    <div class="btn" style="left:197px; top:647px; width:164px; height:54px;">MY FIT</div>
  </section>

  <!-- Loading & results -->
  <section class="screen" style="left:591px; top:993px; height:1152px;">
    <div class="brand">PLENKO</div>
    <div class="loader">
      <div class="abs h-lg" style="top:48px;">LOADING YOUR DATA</div>
      <div class="abs txt" style="top:90px;">This process might take a few minutes</div>
      <div class="abs pct" style="top:141px;">0%</div>
      <div class="bar" style="top:170px;"></div>
      <div class="knob"></div>

      <div class="abs h-sm" style="top:223px;">FUN FACTS ABOUT FEET</div>
      <div class="abs txt-sm" style="top:257px;">Duis aute irure dolor in reprehenderit in voluptate velit esse cillum dolore eu fugiat nulla parpteur sint occaecat</div>
      <div class="rule" style="top:356px;"></div>

      <div class="abs h-sm" style="top:392px;">TELL US YOUR PREFERENCE</div>
      <div class="abs txt" style="top:427px;">How do you prefer the cushion?</div>
      <svg class="chev" style="left:8px;" width="12" height="20" viewBox="0 0 12 20"><path d="M10 2L2 10l8 8" fill="none" stroke="#fff" stroke-width="2"/></svg>
      <div class="segment"><span>SOFT</span><span class="active">MEDIUM</span><span>HARD</span></div>
      <svg class="chev" style="left:327px;" width="12" height="20" viewBox="0 0 12 20"><path d="M2 2l8 8-8 8" fill="none" stroke="#fff" stroke-width="2"/></svg>
      <div class="abs txt-sm" style="top:528px;">Duis aute irure dolor in reprehenderit in voluptate velit esse cillum dolore</div>
      <div class="rule" style="top:605px;"></div>

      <div class="abs h-lg" style="top:635px;">YOU’RE ALL<br>MEASURED UP</div>
      <div class="abs txt" style="top:709px;">This process might take a few minutes</div>
      <div class="abs pct" style="top:757px;">100%</div>
      <div class="bar full" style="top:784px;"></div>
      <div class="abs txt-sm" style="top:825px;">Duis aute irure dolor in reprehenderit in voluptate velit esse cillumeprehenderit in voluptate velit esse cillumdolore</div>
      <div class="btn" style="left:72px; top:918px; width:210px; height:54px;">SEE RESULTS</div>
    </div>
  </section>

</div>
</body>
</html>
```